Business Card Design for Varomir Facility Services

We are looking for a Business Card Design for the Company "Varomir Facility Services."
Front side:
- Company Logo (small)
- Company Name, address, pohone, website and personal data.
- white background, for text e.g. company colors (blue or green like in the logo)
Please use following data:
Company data:
Varomir Facility Services Kostelac
Birkenhaldweg 14
6330 Cham
www.varomir-fs.ch
Person data:
Tarik Kostelac
Geschäftsführer
+41 76 519 47 83
info@varomir-fs.ch
Back side:
could be colored in blue or green
please use a big logo sing and some smaller icons to say what is all beeing offered in facility services, like cleaning, maintenance cleaning
industrial cleaning, caretaking, gardening, disposal. There is no need for everyone of the icons if there are similar or an icon is standing for more of them.
colors to use:
blue: HEX 246BB0
green: HEX 52B33E

```html
<!DOCTYPE html>
<html lang="de">
<head>
<meta charset="utf-8">
<title>Varomir Facility Services – Business Card</title>
<link rel="stylesheet" href="https://fonts.googleapis.com/css2?family=Poppins:wght@400;500;600&display=swap">
<style>
  :root {
    --brand-blue: #0a52b5;
    --brand-blue-light: #2a6db8;
    --brand-green: #52b33e;
    --brand-green-light: #6cc04a;
    --white: #ffffff;
    --stage: #e9e9e9;
  }
  * { box-sizing: border-box; margin: 0; padding: 0; }
  html, body {
    width: 1125px; height: 1200px; overflow: hidden;
    background: var(--stage);
    font-family: "Poppins", sans-serif;
  }
  .card {
    position: absolute; left: 150px; width: 825px; height: 470px;
    overflow: hidden; box-shadow: 0 3px 8px rgba(0,0,0,.25);
  }
  .card--front { top: 100px; background: var(--white); }
  .card--back { top: 632px; background: var(--brand-blue); }
  .card__waves { position: absolute; inset: 0; }

  .wordmark {
    position: absolute; left: 0; right: 0;
    display: flex; align-items: center; justify-content: center; gap: 14px;
    font-weight: 600; font-size: 38px; letter-spacing: .5px;
  }
  .wordmark__dot { width: 26px; height: 26px; border-radius: 50%; background: var(--brand-green); }
  .card--front .wordmark { top: 104px; color: var(--brand-blue-light); }
  .card--back .wordmark { top: 160px; color: var(--white); }

  .person {
    position: absolute; right: 467px; top: 322px; text-align: right;
    color: var(--white); font-size: 20px; line-height: 26px;
  }
  .person__name { color: var(--brand-green-light); font-weight: 600; font-size: 28px; line-height: 36px; }
  .divider {
    position: absolute; left: 385px; top: 318px; width: 1px; height: 116px;
    background: rgba(255,255,255,.55);
  }
  .company {
    position: absolute; left: 413px; top: 326px;
    color: var(--white); font-size: 19.5px; line-height: 26px; list-style: none;
  }
  .company__line { display: flex; align-items: center; gap: 9px; }
  .company__icon { width: 17px; height: 17px; flex: none; }

  .services {
    position: absolute; left: 0; top: 311px; width: 825px; height: 140px; list-style: none;
  }
  .service {
    position: absolute; top: 0; width: 130px; margin-left: -65px;
    text-align: center; color: var(--brand-green-light); font-size: 17px; line-height: 20px;
  }
  .service__badge {
    width: 78px; height: 78px; margin: 0 auto 10px; border-radius: 50%;
    border: 2px solid var(--brand-green-light); padding: 12px;
  }
  .service__art {
    width: 100%; height: 100%; border-radius: 50%;
    background: radial-gradient(circle, rgba(108,192,74,.85), rgba(108,192,74,.35));
  }
</style>
</head>
<body>

<section class="card card--front" aria-label="Front side">
  <svg class="card__waves" viewBox="0 0 825 470" aria-hidden="true">
    <path d="M0,170 Q400,400 825,190 L825,470 L0,470 Z" fill="var(--brand-blue-light)"/>
    <path d="M0,200 Q400,412 860,178 L825,470 L0,470 Z" fill="var(--brand-green)"/>
    <path d="M0,214 Q400,416 840,196 L825,470 L0,470 Z" fill="var(--white)"/>
    <path d="M0,218 Q400,420 840,200 L825,470 L0,470 Z" fill="var(--brand-blue)"/>
  </svg>

  <div class="wordmark"><span class="wordmark__dot"></span>Varomir Facility Services</div>

  <div class="person">
    <p class="person__name">Tarik Kostelac</p>
    <p>Geschäftsführer</p>
    <p>+41 76 519 47 83</p>
  </div>
  <div class="divider"></div>
  <ul class="company">
    <li>Varomir Facility Services Kostelac</li>
    <li>Birkenhaldweg 14, 6330 Cham</li>
    <li class="company__line">
      <svg class="company__icon" viewBox="0 0 16 16" aria-hidden="true"><rect x="1" y="3" width="14" height="10" fill="var(--brand-green-light)"/><path d="M1,3 L8,9 L15,3" fill="none" stroke="var(--brand-blue)" stroke-width="1.4"/></svg>
      info@varomir-fs.ch
    </li>
    <li class="company__line">
      <svg class="company__icon" viewBox="0 0 16 16" aria-hidden="true"><circle cx="8" cy="8" r="7" fill="var(--brand-green-light)"/><path d="M1,8 H15 M8,1 Q3,8 8,15 M8,1 Q13,8 8,15" fill="none" stroke="var(--brand-blue)" stroke-width="1"/></svg>
      www.varomir-fs.ch
    </li>
  </ul>
</section>

<section class="card card--back" aria-label="Back side">
  <div class="wordmark"><span class="wordmark__dot"></span>Varomir Facility Services</div>

  <ul class="services">
    <li class="service" style="left:104px"><div class="service__badge"><div class="service__art" role="img" aria-label="Broom icon"></div></div>Cleaning</li>
    <li class="service" style="left:223px"><div class="service__badge"><div class="service__art" role="img" aria-label="Caretaker icon"></div></div>Caretaking</li>
    <li class="service" style="left:357px"><div class="service__badge"><div class="service__art" role="img" aria-label="Cleaning gloves icon"></div></div>Maintenance<br>cleaning</li>
    <li class="service" style="left:485px"><div class="service__badge"><div class="service__art" role="img" aria-label="Floor cleaner icon"></div></div>Industrial<br>cleaning</li>
    <li class="service" style="left:604px"><div class="service__badge"><div class="service__art" role="img" aria-label="Watering can icon"></div></div>Gardening</li>
    <li class="service" style="left:719px"><div class="service__badge"><div class="service__art" role="img" aria-label="Waste bin icon"></div></div>Disposal</li>
  </ul>
</section>

</body>
</html>
```